Hardcore nerd needs to stand out in a sea of dull Defence business cards

Wombarra Devices is a new Australian consulting engineering company that turns research and theory into practical systems. No evangelistic fluff, just mathematics and physics into electronic and optical circuits for consumer products, scientific research or Defence applications.

We already have a recognised logo (provided) which is often dark blue/black on a light background but we're open to other combinations. (Us engineers tend to have limited aesthetic imagination :)

Some of our recent products have included:
* Instrumentation for electrical testing,
* Radar jammers,
* GPS antenna design,
* Satellite tracking systems,
* High power lasers

We're open to both single and double-sided designs - happy to be convinced either way.

P.S. Another group is working on the web page, so - alas - our web site is currently of no use for images/ideas...

Target Market(s)

Engineering managers,
Scientists

Contact Information for Business Card

Dr Colin Harte
R&D Engineer

colin@wombarradevices.com.au
0427 563 710

PO Box XXX (to be confirmed)
Kelsby ACT 2917
Australia

Font styles to use
Serif
Sans Serif

Colors

Designer to choose colors to be used in the design.

Requirements
Must have
• My contact details!
• I've had many (great) "bold and plain" designs submitted already, so feel free to be artistically creative :)
• Happy to take advice re fonts/colours/printability etc.
Nice to have
• I'm not sure if "lists" are more at home on a CV than a business card, but representative services include:
• Applied electromagnetics
• RF and high speed electronics
• Signal and image processing
• Electro-optical and laser systems
• Concept-to-prototype design services
• If you're considering double sided cards, then often measuring/alignment grids/rulers feature on the back of similar cards.
• e.g. https://www.veltranoptics.example/newgrouppage9.cfm?objectgroup_id=4183
• https://www.veltranoptics.example/newgrouppage9.cfm?objectgroup_ID=4185
• ..or even a "Smith chart" (google will return lots)
• Generic images to represent a capability might work - googling images associated with keyword for each of these areas might help:
• - "passive radar", "phased array", "fdtd", "vircator"
• RF and high speed electronic design
• - "smith chart", "microstrip circuits", "dimensioned drawing", "electronic schematic"
• - "dft", "iir filter"
• - "optical cavity". "laser energy level diagram"
• Background/watermarked images outlines/wireframes/schematics would probably look OK.
Should not have
• If a list of projects/services is provided, it is important not to make the client feel that this is "all" the company can do. Engineering design is a creative discipline (like graphics :)
• Please, no stock "military" snaps like planes, missiles, etc!

```html
<!DOCTYPE html>
<html lang="en">
<head>
<meta charset="utf-8">
<title>Wombarra Devices — Business Card</title>
<link href="https://fonts.googleapis.com/css2?family=Open+Sans:wght@400;700&display=swap" rel="stylesheet">
<style>
  :root {
    --backdrop: #2b241f;
    --card: #141414;
    --card-edge: #0a0a0a;
    --ink: #ffffff;
    --ink-soft: #d6d6d6;
    --rule: #bdbdbd;
    --gloss-dark: #0d0d0d;
    --gloss-mid: #262626;
    --gloss-light: #6a6a6a;
  }
  * { box-sizing: border-box; margin: 0; padding: 0; }
  html, body {
    width: 1200px; height: 716px; overflow: hidden;
    background: var(--backdrop);
    font-family: "Open Sans", Arial, sans-serif;
    color: var(--ink);
  }
  .canvas {
    position: relative; width: 1200px; height: 716px;
    display: flex; align-items: center; justify-content: center; gap: 40px;
  }
  .card {
    position: relative; width: 520px; height: 298px;
    background: var(--card);
    border: 1px solid var(--card-edge);
    overflow: hidden;
  }

  /* Front */
  .brand {
    position: absolute; display: flex; align-items: center; gap: 10px;
  }
  .brand__dot {
    width: 38px; height: 38px; border-radius: 50%; background: var(--ink);
    flex: none;
  }
  .brand__name {
    font-weight: 700; color: var(--ink); text-transform: uppercase;
    letter-spacing: 0.08em; line-height: 1.05;
  }
  .card--front .brand { top: 52px; right: 34px; }
  .card--front .brand__name { font-size: 18px; }

  .person { position: absolute; left: 34px; top: 118px; }
  .person__name {
    font-weight: 700; font-size: 15px; letter-spacing: 0.04em; text-transform: uppercase;
  }
  .person__role { font-size: 10px; color: var(--ink-soft); margin-top: 1px; }

  .divider {
    position: absolute; left: 34px; right: 34px; top: 162px;
    height: 1px; background: var(--rule);
  }
  .contact {
    position: absolute; left: 34px; top: 176px;
    list-style: none; font-size: 10px; color: var(--ink-soft);
  }
  .contact li { display: flex; align-items: center; gap: 7px; margin-bottom: 4px; }
  .contact svg { width: 9px; height: 9px; fill: var(--ink-soft); flex: none; }

  .address {
    position: absolute; right: 34px; top: 124px;
    font-size: 11px; line-height: 1.45; color: var(--ink-soft); text-align: left;
  }

  /* Back */
  .pattern {
    position: absolute; inset: 0;
    background: linear-gradient(120deg,
      var(--gloss-dark) 0%, var(--gloss-dark) 45%,
      var(--gloss-mid) 62%, var(--gloss-light) 100%);
  }
  .card--back .brand {
    top: 50%; left: 50%; transform: translate(-40%, -50%);
  }
  .card--back .brand__dot { width: 58px; height: 58px; }
  .card--back .brand__name { font-size: 26px; }
</style>
</head>
<body>
<main class="canvas">

  <section class="card card--front" aria-label="Card front">
    <div class="brand">
      <span class="brand__dot"></span>
      <span class="brand__name">Wombarra<br>Devices</span>
    </div>

    <div class="person">
      <p class="person__name">Dr Colin Harte</p>
      <p class="person__role">R&amp;D Engineer</p>
    </div>

    <address class="address">PO Box XXX<br>Kelsby ACT 2917, Australia</address>

    <div class="divider"></div>

    <ul class="contact">
      <li>
        <svg viewBox="0 0 24 24" aria-hidden="true"><path d="M6.6 10.8a15.1 15.1 0 0 0 6.6 6.6l2.2-2.2c.3-.3.7-.4 1-.2 1.1.4 2.3.6 3.6.6.6 0 1 .4 1 1V20c0 .6-.4 1-1 1A17 17 0 0 1 3 4c0-.6.4-1 1-1h3.5c.6 0 1 .4 1 1 0 1.3.2 2.5.6 3.6.1.3 0 .7-.2 1z"/></svg>
        0427 563 710
      </li>
      <li>
        <svg viewBox="0 0 24 24" aria-hidden="true"><path d="M2 5h20v14H2zm2 2v.5l8 5 8-5V7zm0 3v7h16v-7l-8 5z"/></svg>
        colin@wombarradevices.com.au
      </li>
    </ul>
  </section>

  <section class="card card--back" aria-label="Card back">
    <div class="pattern" role="img" aria-label="Repeating tonal pattern of the company mark in spot gloss, fading from black to grey"></div>
    <div class="brand">
      <span class="brand__dot"></span>
      <span class="brand__name">Wombarra<br>Devices</span>
    </div>
  </section>

</main>
</body>
</html>
```